Business Card Design for my Real Estate Investing Company

This is for a Real Estate Investing Company that will be serving the Las Vegas Valley. Id like the following slogan included: "Investing in Our Community" I have attached my logo. You will see the color tones I'm interested in..in my logo. I would like the card to be double-sided with a modern, professional look.
Target Market(s)
Homeowners, banks, real estate industry
Industry/Entity Type
Real Estate
Contact Information for Business Card
name: Dale Harwick
position: Managing Member
address: 4821 Corliss Pkwy ste 207-300
N. Las Vegas, NV 89084
phone: (702) 555-0143
fax: (702) 555-0187
email: SummitRidgeEstate@hollowmail.test
web: SummitRidgeEstates.test
*At the bottom of the card I would like....
We buy houses for cash....no repairs, no commissions, no fees!
Logo Text
SUMMIT RIDGE ESTATES "Investing in Our Community"
Font styles to use
Other font styles liked:
- Lora
Requirements
Must have
- On the back of the card, i'd like to have my logo large and the following statements:
- Are you considering selling your home? Want a simple, hassle-free transaction? We can help! We buy houses for cash and can close quickly! No need to do any repairs, no realtor commissions, no closing costs.....and no headaches. Let us help you with your real estate needs...!
Nice to have
- multiple colors 2 two tone on front and back

```html
<!DOCTYPE html>
<html lang="en">
<head>
<meta charset="utf-8">
<title>Summit Ridge Estates – Business Card</title>
<link rel="stylesheet" href="https://fonts.googleapis.com/css2?family=Lora:ital,wght@0,400;0,700;1,400&display=swap">
<style>
  :root {
    --stage: #333333;
    --card-light: #f2f2f2;
    --brand-blue: #0b54a8;
    --ink: #1a1a1a;
    --white: #ffffff;
  }
  * { box-sizing: border-box; margin: 0; padding: 0; }
  html, body { width: 1200px; height: 750px; overflow: hidden; }
  body {
    background: var(--stage);
    font-family: "Lora", Georgia, serif;
    display: flex;
    align-items: center;
    justify-content: center;
    gap: 24px;
  }
  .card {
    width: 570px;
    height: 327px;
    position: relative;
    overflow: hidden;
  }
  .card--front { background: var(--card-light); color: var(--ink); }
  .card--back { background: var(--brand-blue); color: var(--white); text-align: center; }

  .brand { display: flex; align-items: center; gap: 10px; }
  .brand-mark { width: 16px; height: 16px; flex: none; }
  .brand-name { font-weight: 700; letter-spacing: 0.5px; line-height: 1; }
  .slogan {
    font-style: italic;
    letter-spacing: 3px;
    font-size: 11.5px;
    margin-top: 8px;
  }

  .card--front .brand-wrap { position: absolute; left: 46px; top: 52px; }
  .card--front .brand-mark { background: var(--brand-blue); }
  .card--front .brand-name { color: var(--brand-blue); font-size: 27px; }
  .card--front .slogan { color: var(--ink); padding-left: 2px; }

  .person { position: absolute; left: 43px; top: 138px; font-size: 16px; }
  .person-name { color: var(--brand-blue); text-transform: uppercase; }

  .contacts { position: absolute; left: 44px; top: 172px; list-style: none; font-size: 14px; }
  .contacts li { display: flex; align-items: center; gap: 6px; height: 19.5px; }
  .contacts svg { width: 12px; height: 12px; fill: var(--brand-blue); flex: none; }

  .address { position: absolute; left: 43px; top: 253px; font-size: 14.5px; }

  .tagline-bar {
    position: absolute; left: 28px; top: 278px;
    width: 515px; height: 23px;
    background: var(--brand-blue);
    color: var(--white);
    border-radius: 12px;
    font-size: 15.5px;
    line-height: 23px;
    padding-left: 14px;
  }

  .card--back .brand-wrap { position: absolute; left: 0; right: 0; top: 70px; display: flex; flex-direction: column; align-items: center; }
  .card--back .brand-mark { background: var(--white); }
  .card--back .brand-name { color: var(--white); font-size: 32px; }
  .card--back .slogan { color: var(--white); }

  .pitch { position: absolute; left: 0; right: 0; top: 160px; font-size: 14.5px; line-height: 21px; }
  .pitch-highlight { font-size: 20px; line-height: 24px; margin-bottom: 9px; }
</style>
</head>
<body>

  <section class="card card--front" aria-label="Business card front">
    <div class="brand-wrap">
      <div class="brand">
        <span class="brand-mark"></span>
        <span class="brand-name">SUMMIT RIDGE ESTATES</span>
      </div>
      <p class="slogan">"Investing in Our Community"</p>
    </div>

    <p class="person"><span class="person-name">Dale Harwick</span>-Managing Member</p>

    <ul class="contacts">
      <li>
        <svg viewBox="0 0 12 12" aria-hidden="true"><rect x="0" y="0" width="12" height="12" rx="1.5"/><path d="M3.2 2.5c.4-.3.9-.2 1.1.2l.6 1.2c.2.4 0 .7-.3.9l-.4.3c.4 1 1.2 1.9 2.2 2.4l.3-.4c.2-.3.6-.4.9-.2l1.1.7c.4.2.5.7.2 1.1l-.5.6c-.4.4-1 .5-1.6.3C4.8 8.8 3.1 7 2.5 4.9c-.2-.6 0-1.2.4-1.6z" fill="#f2f2f2"/></svg>
        (702) 555-0143
      </li>
      <li>
        <svg viewBox="0 0 12 12" aria-hidden="true"><rect x="3" y="0.5" width="6" height="3"/><rect x="0.5" y="4" width="11" height="5" rx="1"/><rect x="3" y="7.5" width="6" height="4" fill="#f2f2f2" stroke="#0b54a8" stroke-width="1"/></svg>
        (702) 555-0187
      </li>
      <li>
        <svg viewBox="0 0 12 12" aria-hidden="true"><rect x="0.5" y="2" width="11" height="8"/><path d="M0.8 2.4L6 6.6l5.2-4.2" fill="none" stroke="#f2f2f2" stroke-width="1"/></svg>
        SummitRidgeEstate@hollowmail.test
      </li>
      <li>
        <svg viewBox="0 0 12 12" aria-hidden="true"><circle cx="6" cy="6" r="5.5"/><g fill="none" stroke="#f2f2f2" stroke-width="0.7"><ellipse cx="6" cy="6" rx="2.3" ry="5.5"/><path d="M0.5 6h11M1.3 3.3h9.4M1.3 8.7h9.4"/></g></svg>
        SummitRidgeEstates.test
      </li>
    </ul>

    <p class="address">4821 Corliss Pkwy ste 207-300 N. Las Vegas, NV 89084</p>

    <p class="tagline-bar">We buy houses for cash....no repairs, no commissions, no fees!</p>
  </section>

  <section class="card card--back" aria-label="Business card back">
    <div class="brand-wrap">
      <div class="brand">
        <span class="brand-mark"></span>
        <span class="brand-name">SUMMIT RIDGE ESTATES</span>
      </div>
      <p class="slogan">"Investing in Our Community"</p>
    </div>

    <div class="pitch">
      <p>Are you considering selling your home?</p>
      <p>Want a simple, hassle-free transaction?</p>
      <p class="pitch-highlight">We can help!</p>
      <p>We buy houses for cash and can close quickly!</p>
      <p>No need to do any repairs, no realtor commissions, no closing costs.....</p>
      <p>and no headaches. Let us help you with your real estate needs...!</p>
    </div>
  </section>

</body>
</html>
```